Desktop and Networking Support Course 9.17.25

Important the ad should not be very busy with the text taking up the major part of the ad .. please do not make the text so big that it takes up most of the ad..
Flyer Design Brief for Graphic Artist
also i am looking for something unique or creative that it will stand out .
Size & Layout:
Full Page with Bleed: 8” x 10.75” + 0.25” bleed on all sides.
Footer Space: Leave a 1-inch margin at the bottom for footer content (e.g., contact info, logo, or call-to-action).
Target Audience:
College-age students (around 24 years old)
Located in the USA
Interested in creative, professional, and career-building opportunities
Purpose:
To attract students to enroll in a college program
Flyer should be eye-catching, unique, and creative
Text must be clear and readable,
Design Style:
Use vector art, typography, or photography — your choice
If using photography, feature a white young professional USA citizen:
Wearing a white collared shirt
not with long hair
Creative Direction:
The flyer should stand out visually — something people would want to look at and keep
Showcase creativity and professionalism
Use bold colors, dynamic layout, or unexpected design elements to grab attention
Avoid clutter — keep the design balanced and clean
Text Suggestions (can be adjusted):
Footer,
please leave one inch on the bottom for the footer

```html
<!DOCTYPE html>
<html lang="en">
<head>
<meta charset="utf-8">
<title>Desktop &amp; Network Support Course</title>
<link href="https://fonts.googleapis.com/css2?family=Oswald:wght@500;600&family=Figtree:wght@400;600;700;800&display=swap" rel="stylesheet">
<style>
  :root {
    --navy: #17253b;
    --pink: #f7034f;
    --pink-soft: #f6709b;
    --ink: #111111;
    --white: #ffffff;
    --photo-light: #eef0f5;
    --photo-mid: #d9dde6;
  }
  html, body { margin: 0; padding: 0; overflow: hidden; }
  body { width: 927px; height: 1200px; background: var(--white); }
  .flyer {
    position: relative; width: 927px; height: 1200px; overflow: hidden;
    background: var(--white); font-family: "Figtree", sans-serif; color: var(--ink);
  }
  .backdrop { position: absolute; inset: 0; }
  .brand {
    position: absolute; left: 29px; top: 22px; margin: 0;
    font-family: "Figtree", sans-serif; font-weight: 800; font-size: 29px;
    letter-spacing: 1px; color: var(--white);
  }
  .portrait {
    position: absolute; left: 405px; top: 44px; width: 522px; height: 920px;
    border-radius: 260px 0 0 40px;
    background: radial-gradient(ellipse at 60% 35%, var(--photo-light) 0%, var(--photo-mid) 60%, rgba(217,221,230,0) 100%);
  }
  .headline {
    position: absolute; left: 26px; top: 144px; margin: 0;
    font-family: "Oswald", sans-serif; font-weight: 600; font-size: 66px;
    line-height: 88px; color: var(--navy); letter-spacing: 1px; white-space: nowrap;
  }
  .headline .click { color: var(--pink); font-size: 79px; letter-spacing: 0; }
  .click-underline {
    position: absolute; left: 225px; top: 312px; width: 173px; height: 4px; background: var(--pink);
  }
  .course-name {
    position: absolute; left: 26px; top: 359px; margin: 0;
    font-weight: 600; font-size: 27px; color: var(--ink);
  }
  .divider {
    position: absolute; left: 0; width: 440px; height: 3px;
    background: linear-gradient(90deg, var(--pink), rgba(247,3,79,0));
  }
  .divider.first { top: 427px; }
  .divider.second { top: 637px; }
  .feature-number {
    position: absolute; left: 24px; margin: 0;
    font-family: "Oswald", sans-serif; font-weight: 600; font-size: 78px; line-height: 1;
    -webkit-background-clip: text; background-clip: text; color: transparent;
  }
  .feature-number.one { top: 461px; background-image: linear-gradient(180deg, var(--pink) 35%, rgba(247,3,79,0.05) 100%); }
  .feature-number.two { top: 672px; background-image: linear-gradient(180deg, var(--navy) 30%, rgba(23,37,59,0.05) 100%); }
  .feature-title {
    position: absolute; margin: 0;
    font-family: "Oswald", sans-serif; font-weight: 500; font-size: 26px;
    line-height: 35px; color: var(--ink);
  }
  .feature-title.one { left: 115px; top: 459px; }
  .feature-title.two { left: 120px; top: 674px; }
  .stat {
    position: absolute; left: 116px; top: 504px; margin: 0;
    font-weight: 600; font-size: 20px; color: var(--pink);
  }
  .detail {
    position: absolute; left: 26px; margin: 0;
    font-size: 19px; line-height: 31px; letter-spacing: 0.4px; color: var(--ink);
  }
  .detail strong { font-weight: 700; }
  .detail.one { top: 547px; }
  .detail.two { top: 760px; line-height: 30px; }
  .format-band {
    position: absolute; left: 0; top: 841px; width: 927px; height: 181px;
    background: linear-gradient(90deg, #b9bcc2 0%, #5a6475 22%, var(--navy) 45%, var(--navy) 100%);
  }
  .format-pill {
    position: absolute; left: 0; top: 876px; width: 110px; height: 88px;
    border-radius: 0 44px 44px 0; background: var(--pink);
  }
  .format-pill svg { position: absolute; left: 26px; top: 14px; }
  .format-text {
    position: absolute; left: 124px; top: 874px; margin: 0;
    font-weight: 400; font-size: 29px; line-height: 44px; letter-spacing: -0.5px; color: var(--white);
  }
  .scholarship-seal { position: absolute; left: 588px; top: 760px; width: 304px; height: 304px; }
  .seal-text {
    position: absolute; left: 588px; top: 900px; width: 304px; margin: 0; text-align: center;
    font-weight: 800; font-size: 30px; line-height: 38px; color: var(--white);
  }
</style>
</head>
<body>
<main class="flyer">
  <svg class="backdrop" width="927" height="1200" viewBox="0 0 927 1200" aria-hidden="true">
    <path d="M0,0 L245,0 Q95,55 0,186 Z" fill="var(--pink)"/>
    <path d="M0,0 L120,0 Q45,32 0,72 Z" fill="var(--navy)"/>
    <path d="M927,40 Q905,230 862,360 Q900,395 927,425 Z" fill="var(--pink-soft)"/>
    <path d="M0,1173 Q560,1110 927,800 L927,1200 L0,1200 Z" fill="var(--pink)"/>
    <path d="M90,1200 Q600,1120 927,865 L927,1200 Z" fill="var(--navy)"/>
  </svg>

  <p class="brand">LOGO</p>

  <div class="portrait" role="img" aria-label="Smiling young professional with glasses and a beard, wearing a white collared shirt, arms crossed"></div>

  <div class="format-band"></div>

  <h1 class="headline">YOUR CAREER IS<br>JUST A <span class="click">CLICK</span> AWAY</h1>
  <div class="click-underline"></div>
  <p class="course-name">Desktop &amp; Network Support Course</p>

  <div class="divider first"></div>
  <p class="feature-number one">01</p>
  <h2 class="feature-title one">MASTER NIMBUS OPERATING SYSTEMS</h2>
  <p class="stat">90% Employment Rate - Class of 2024</p>
  <p class="detail one">Prepare for 3 of the <strong>Top 10 Tech Jobs</strong><br>National Career <strong>Review 2025</strong></p>

  <div class="divider second"></div>
  <p class="feature-number two">02</p>
  <h2 class="feature-title two">HANDS-ON DESKTOP &amp;<br>NETWORK TRAINING</h2>
  <p class="detail two">Real-World <strong>Troubleshooting Skills</strong><br>Ready for <strong>IT Jobs</strong></p>

  <div class="format-pill">
    <svg width="56" height="60" viewBox="0 0 56 60" aria-hidden="true" fill="none" stroke="#fff" stroke-width="2.4">
      <path d="M2,10 Q12,2 22,10"/><path d="M7,14 Q12,10 17,14"/>
      <path d="M12,30 L34,12 L56,30" stroke-linejoin="round"/>
      <rect x="14" y="28" width="40" height="30" fill="#fff" stroke="none"/>
      <circle cx="34" cy="37" r="5" stroke="var(--pink)"/>
      <path d="M26,52 Q34,42 42,52" stroke="var(--pink)"/>
    </svg>
  </div>
  <p class="format-text">In-Person &amp; Remote<br>Options</p>

  <svg class="scholarship-seal" viewBox="0 0 304 304" aria-hidden="true">
    <circle cx="152" cy="152" r="148" fill="var(--pink)" stroke="#fff" stroke-width="4" stroke-dasharray="14 6"/>
    <circle cx="152" cy="152" r="126" fill="none" stroke="#fff" stroke-width="3"/>
    <path d="M152,44 L200,66 L152,88 L104,66 Z" fill="#fff"/>
    <path d="M122,78 L122,100 Q152,116 182,100 L182,78 L152,92 Z" fill="#fff"/>
    <path d="M108,68 L108,96" stroke="#fff" stroke-width="3"/>
    <rect x="104" y="96" width="8" height="10" fill="#fff"/>
    <path d="M112,112 L192,112 L188,124 L116,124 Z" fill="#fff"/>
  </svg>
  <p class="seal-text">Partial<br>Scholarships<br>Offered</p>
</main>
</body>
</html>
```